QRV Advisors needs a web site

We need a web site for www.qrvadvisors-example.com. QRV is a mergers and acquisition consulting company that focuses our buyer and seller services on logistics companies. We help put companies together, and help with legal and financial due diligence. We want the web site to express our service and show the logistics components. We want personalized images versus pictures of trucks and airplanes.

Our new logo uses Burgandy and grey colors. Image attached. We are not in to bold, big letters...classy, artistic, low key preferred. Confidentiality, experience, professional are what we want to express on the site.

All we expect for the first part of this project is a home page, and one subpage.  We are budgeting other funds for the technical aspects of the web site

Reason: All that I'm seeing so far is trucks, forklifts and planes. We are a legal mergers and acquisitions firm that focus on logistics. I like some of the images to say logistics, but really want it say legal, financial, and putting companies together. Will pay extra for the sub page if someone can impress us with a home page.

Reason: Swamped with another project at the moment...will work on this over the weekend and provide designer feedback and select final design by Tuesday

```html
<!DOCTYPE html>
<html lang="en">
<head>
<meta charset="utf-8">
<title>QRV Advisors — Home</title>
<link href="https://fonts.googleapis.com/css2?family=Lato:wght@400;700&family=Cinzel:wght@400;600&family=Oswald:wght@400&display=swap" rel="stylesheet">
<style>
:root{
  --burgundy:#a0102f;
  --burgundy-dark:#7e0a24;
  --grey-text:#4a4a4a;
  --grey-light:#e9e9e9;
  --ink:#2a2a2a;
  --panel-dark:#1f1f1f;
  --footer:#2c2c2c;
  --white:#fff;
}
*{box-sizing:border-box;margin:0;padding:0}
html,body{width:962px;height:1200px;overflow:hidden}
body{position:relative;background:#f7f7f7;font-family:"Lato",sans-serif;color:var(--grey-text)}
.abs{position:absolute}

/* header */
.site-header{left:0;top:0;width:962px;height:90px;background:linear-gradient(#fff,#ececec)}
.brand{left:108px;top:26px;display:flex;align-items:center;gap:10px}
.brand-mark{width:30px;height:30px;background:var(--burgundy)}
.brand-name{font-size:27px;font-weight:400;color:var(--grey-text);letter-spacing:.5px}
.header-phone{right:106px;top:14px;font-size:13px;color:var(--grey-text);display:flex;gap:5px;align-items:center}
.main-nav{left:392px;top:62px;display:flex;align-items:center;font-size:12.5px;color:var(--ink)}
.main-nav a{padding:2px 12px;border-left:1px solid #ddd;text-decoration:none;color:inherit}
.main-nav a:first-child{border:0}
.main-nav a.active{background:var(--burgundy);color:#fff;font-weight:700;border-radius:2px;padding:3px 7px;margin-right:6px}

/* hero */
.hero{left:0;top:90px;width:962px;height:361px;background:linear-gradient(180deg,#4d78b0 0%,#9fb7d2 40%,#8c8680 75%,#a79385 100%)}
.slide{left:105px;top:113px;width:752px;height:292px;background:#fff;padding:4px;box-shadow:0 2px 6px rgba(0,0,0,.3)}
.slide-photo{width:100%;height:100%;background:linear-gradient(100deg,#7d8890 0%,#b9b3aa 45%,#c7cfd8 70%,#8fa0b6 100%)}
.slide-caption{left:109px;top:292px;width:356px;height:86px;background:linear-gradient(90deg,rgba(15,15,15,.92),rgba(15,15,15,.55));color:#fff;font-family:"Cinzel",serif;font-size:20px;line-height:25px;text-align:center;padding-top:5px}
.slider-dots{left:425px;top:405px;width:112px;height:27px;background:#e6e6e6;border-radius:0 0 14px 14px;display:flex;justify-content:center;align-items:center;gap:8px;box-shadow:0 2px 3px rgba(0,0,0,.25)}
.slider-dots i{width:10px;height:10px;border-radius:50%;background:#666}
.slider-dots i.on{background:var(--burgundy)}

/* services */
.service{top:481px;width:180px;text-align:center}
.service-icon{width:86px;height:86px;border-radius:50%;border:1px solid #ccc;background:#fff;margin:0 auto;display:flex;align-items:center;justify-content:center}
.service-icon.active{background:var(--burgundy);border-color:var(--burgundy)}
.service h3{font-size:16px;font-weight:400;color:var(--ink);margin-top:14px}
.service p{font-size:11.5px;line-height:14.5px;margin-top:5px}
.btn{display:inline-block;background:var(--burgundy);color:#fff;font-size:11.5px;font-weight:700;padding:2px 7px;margin-top:11px}
.news-input{width:166px;height:22px;border:1px solid #bbb;background:#fff;font-size:10.5px;color:#999;text-align:left;padding:4px 7px;margin:7px auto 0}
.rule{left:110px;top:693px;width:742px;height:1px;background:linear-gradient(90deg,transparent,#ddd,transparent)}

/* panels */
.panel{top:720px;height:225px;background:#fff;border:1px solid #e2e2e2;box-shadow:0 6px 6px -4px rgba(0,0,0,.25);z-index:2}
.panel-head{position:absolute;left:-5px;right:-5px;top:10px;height:30px;background:linear-gradient(90deg,#2a2a2a,#111);color:#fff;font-family:"Cinzel",serif;font-size:15.5px;letter-spacing:1px;padding:6px 10px}
.panel-head .badge{position:absolute;right:8px;top:2px;width:27px;height:27px;border-radius:50%;background:#fff;display:flex;align-items:center;justify-content:center}
.panel-head .badge i{width:19px;height:19px;border-radius:50%;background:var(--burgundy)}
.panel-body{position:absolute;left:12px;right:12px;top:54px;font-size:11px;line-height:16px}
.panel-photo{height:86px;background:linear-gradient(100deg,#6d6f74,#b9bcc2 50%,#8a8d93)}
.more{position:absolute;right:12px;bottom:8px;color:var(--burgundy);font-size:10.5px;font-weight:700}
.news-item{display:flex;gap:6px;padding-bottom:5px;margin-bottom:5px;border-bottom:1px dotted #ccc;font-size:10.5px;line-height:14px}
.news-item:last-of-type{border:0}
.date{width:30px;flex:none;text-align:center;font-weight:700;color:#fff}
.date b{display:block;background:var(--burgundy);font-size:11.5px;line-height:16px}
.date span{display:block;background:#666;font-size:8.5px;line-height:11px}
.news-item strong{color:var(--ink);font-size:11px}
.avatar{float:left;width:70px;height:70px;border-radius:50%;border:2px solid #ddd;background:linear-gradient(160deg,#9a8a7d,#5f6d80);margin:0 12px 4px 0}
.quote-title{color:var(--ink);font-weight:700}

/* footer */
.footer-wave{left:0;top:900px;z-index:1}
.footer-links{top:1113px;font-size:11px;color:#fff;line-height:22px;z-index:2;list-style:none}
.footer-links li::before{content:"•";color:#aaa;margin-right:5px;font-size:8px}
.footer-map{left:384px;top:1084px;width:190px;height:70px;border:2px solid #999;background:linear-gradient(135deg,#d8d2c2,#e8b36a 50%,#b9c6d4);z-index:2}
.footer-address{left:382px;top:1160px;display:flex;gap:7px;color:#fff;font-size:10.5px;line-height:13.5px;z-index:2}
.cta{left:623px;top:1060px;color:#fff;font-family:"Oswald",sans-serif;font-size:14px;line-height:24px;z-index:2}
.cta .appt{display:inline-block;background:linear-gradient(#fff,#ddd);color:var(--ink);padding:0 7px;line-height:20px;margin-left:4px;border:1px solid #999}
.social{left:682px;top:1129px;display:flex;gap:10px;z-index:2}
.social i{width:18px;height:18px;border-radius:50%;background:#cfcfcf}
.copyright{left:650px;top:1174px;font-size:9.5px;color:#ddd;z-index:2}
</style>
</head>
<body>

<header class="site-header abs"></header>
<div class="brand abs"><span class="brand-mark"></span><span class="brand-name">QRV Advisors</span></div>
<div class="header-phone abs">
  <svg width="12" height="12" viewBox="0 0 24 24"><path d="M6.6 10.8c1.4 2.8 3.8 5.1 6.6 6.6l2.2-2.2c.3-.3.7-.4 1-.2 1.1.4 2.3.6 3.6.6.6 0 1 .4 1 1V20c0 .6-.4 1-1 1C10.6 21 3 13.4 3 4c0-.6.4-1 1-1h3.5c.6 0 1 .4 1 1 0 1.3.2 2.5.6 3.6.1.3 0 .7-.2 1z" fill="#a0102f"/></svg>
  555 010 2040
</div>
<nav class="main-nav abs">
  <a class="active">Home</a><a>About</a><a>Consulting Services</a><a>News &amp; Events</a><a>FAQ's</a><a>Contact</a>
</nav>

<section class="hero abs" role="img" aria-label="Background scene of a logistics yard with trucks and dock workers"></section>
<div class="slide abs"><div class="slide-photo" role="img" aria-label="Smiling businessman in an office with colleagues behind him"></div></div>
<div class="slide-caption abs">We are a legal mergers<br>and acquisitions firm that<br>focus on logistics.</div>
<div class="slider-dots abs"><i class="on"></i><i></i><i></i><i></i></div>

<div class="service abs" style="left:106px">
  <div class="service-icon active"><svg width="40" height="36" viewBox="0 0 40 36"><rect x="2" y="4" width="28" height="26" rx="2" fill="#fff"/><rect x="6" y="10" width="20" height="2" fill="#a0102f"/><circle cx="29" cy="24" r="9" fill="#fff" stroke="#a0102f" stroke-width="2"/><path d="M29 18v6h5" stroke="#a0102f" stroke-width="2" fill="none"/></svg></div>
  <h3>Business Planning</h3>
  <p>Lorem ipsum dolor sit amet, consect ectetuer adipiscing elit, sed diamgra nonummy.</p>
  <span class="btn">Read More</span>
</div>
<div class="service abs" style="left:287px">
  <div class="service-icon"><svg width="44" height="40" viewBox="0 0 44 40"><circle cx="28" cy="9" r="7" fill="#222"/><path d="M16 38c0-12 6-18 12-18s12 6 12 18z" fill="#222"/><rect x="4" y="20" width="20" height="15" fill="#fff" stroke="#222" stroke-width="2"/><path d="M9 31v-5M13 31v-8M17 31v-6" stroke="#222" stroke-width="2"/></svg></div>
  <h3>Business Merger</h3>
  <p>Lorem ipsum dolor sit amet, consect ectetuer adipiscing elit, sed diamgra nonummy.</p>
  <span class="btn">Read More</span>
</div>
<div class="service abs" style="left:481px;width:190px">
  <div class="service-icon"><svg width="40" height="44" viewBox="0 0 40 44"><rect x="6" y="2" width="28" height="20" fill="#fff" stroke="#222" stroke-width="2"/><path d="M24 16v-4M28 16v-8" stroke="#222" stroke-width="2"/><circle cx="16" cy="9" r="3" fill="#222"/><path d="M13 13h6v10h-6z" fill="#222"/><circle cx="8" cy="31" r="4" fill="#222"/><circle cx="20" cy="31" r="4" fill="#222"/><circle cx="32" cy="31" r="4" fill="#222"/><path d="M2 42c0-6 12-6 12 0zM14 42c0-6 12-6 12 0zM26 42c0-6 12-6 12 0z" fill="#222"/></svg></div>
  <h3>Acquisition (M&amp;A) Advisory</h3>
  <p>Lorem ipsum dolor sit amet, consect ectetuer adipiscing elit, sed diamgra nonummy.</p>
  <span class="btn">Read More</span>
</div>
<div class="service abs" style="left:675px">
  <div class="service-icon"><svg width="42" height="28" viewBox="0 0 42 28"><rect x="1" y="1" width="40" height="26" fill="#222"/><path d="M1 1l20 15 20-15M1 27l15-13M41 27l-15-13" stroke="#fff" stroke-width="2" fill="none"/></svg></div>
  <h3>Newsletter Signup</h3>
  <div class="news-input">Enter your email here</div>
  <p style="margin-top:11px">Signup for QRV Newsletter!</p>
  <span class="btn" style="margin-top:8px">Subscribe</span>
</div>
<div class="rule abs"></div>

<section class="panel abs" style="left:109px;width:232px">
  <div class="panel-head">What we do<span class="badge"><i></i></span></div>
  <div class="panel-body">
    <div class="panel-photo" role="img" aria-label="Team of business professionals seated around a meeting table"></div>
    <p style="margin-top:7px">QRV can help you formulate and execute your growth strategy. We take a strategic and consultative approach...</p>
  </div>
  <span class="more">Read More</span>
</section>

<section class="panel abs" style="left:366px;width:232px">
  <div class="panel-head">News &amp; Events<span class="badge"><i></i></span></div>
  <div class="panel-body" style="top:52px">
    <div class="news-item"><div class="date"><b>22</b><span>JULY</span></div><div><strong>Duis aute irure dolor in repre</strong><br>Duis autem vel eum iriure dolor inbo dolor hendrerit in amet vulputate.</div></div>
    <div class="news-item"><div class="date"><b>22</b><span>JULY</span></div><div><strong>Duis aute irure dolor in repre</strong><br>Duis autem vel eum iriure dolor inbo dolor hendrerit in amet vulputate.</div></div>
    <div class="news-item"><div class="date"><b>22</b><span>JULY</span></div><div><strong>Duis aute irure dolor in repre</strong><br>Duis autem vel eum iriure dolor inbo dolor hendrerit in amet vulputate.</div></div>
  </div>
  <span class="more">Read More</span>
</section>

<section class="panel abs" style="left:622px;width:232px">
  <div class="panel-head">Client Testimonials<span class="badge"><i></i></span></div>
  <div class="panel-body" style="top:58px;font-size:10.5px">
    <div class="avatar" role="img" aria-label="Portrait photo of the client"></div>
    <p><span class="quote-title">“ Lorem ipsum dolor sita</span><br>Sed diam nonummy euismli tincidunt laorlpi dolore smit aliquam erat volutpat.</p>
    <p style="clear:both;padding-top:6px">Duis autem vel eum iriure dolor in dolor hend sit in amet sit vulputate velit uisam.</p>
    <p class="quote-title" style="margin-top:4px">- Mr. Client Name</p>
  </div>
  <span class="more">Read More</span>
</section>

<svg class="footer-wave abs" width="962" height="300" viewBox="0 0 962 300" aria-hidden="true">
  <defs><linearGradient id="dark" x1="0" y1="0" x2="0" y2="1"><stop offset="0" stop-color="#3a3a3a"/><stop offset="1" stop-color="#222"/></linearGradient></defs>
  <path d="M0 20C110 150 300 180 480 150 680 115 820 78 962 68V300H0Z" fill="#d6d6d6"/>
  <path d="M0 30C115 160 300 188 480 160 680 126 820 90 962 80V300H0Z" fill="#9b0f2e"/>
  <path d="M0 70C115 182 300 206 480 180 680 150 820 112 962 102V300H0Z" fill="#ececec"/>
  <path d="M0 80C115 190 300 212 480 188 680 160 820 122 962 112V300H0Z" fill="url(#dark)"/>
</svg>

<ul class="footer-links abs" style="left:114px"><li>Home</li><li>About</li><li>Consulting Services</li></ul>
<ul class="footer-links abs" style="left:232px"><li>News &amp; Events</li><li>FAQ's</li><li>Contact</li></ul>
<div class="footer-map abs" role="img" aria-label="Map of the office location"></div>
<div class="footer-address abs">
  <svg width="14" height="20" viewBox="0 0 14 20"><path d="M7 0a7 7 0 0 0-7 7c0 5 7 13 7 13s7-8 7-13a7 7 0 0 0-7-7zm0 10a3 3 0 1 1 0-6 3 3 0 0 1 0 6z" fill="#fff"/></svg>
  <div>QRV Advisors<br>Harbor City, Bayport, Lakeview.</div>
</div>
<div class="cta abs">Schedule Free Consultation <span class="appt">Appointment</span><br>Or Call Us on : (555) 010 2040</div>
<div class="social abs"><i></i><i></i><i></i><i></i></div>
<div class="copyright abs">© Copyright 2013 QRV Advisors.</div>

</body>
</html>
```